Specialized Personal Trainer Needs a Business Card Design

I need a business card design for my personal training business called Tall Oak Fitness. I have my Human Kinetics degree in Exercise Science from the Halvering Polytechnic Institute as well as an extra certification from NFBP (National Federation of Body Practice). I work as a Cardiac Rehab Exercise Specialist and personal trainer giving specialized exercise prescriptions to those that have different heart conditions as well as work with the general population in weight loss, strength and conditioning, getting/staying fit.
Updates

I decided that I wanted a logo (as I did not have one before I submitted my project for a business card) so I am submitting a project to get a logo done and then I will decide on a business card, hopefully being able to use one of the designs already submitted.  My apologies for doing this backwards.  I am new to this so I appreciate your patience.

Thank you.

Hi, I have just created a project for a logo design (I realized I needed a logo and I should've done that first..oops!), please feel free to participate.  Once I receive a logo I like I will finalize my business card project and hopefully incorporate it into one of your business card designs. 

Thank you!

Target Market(s)

Business professionals

Industry/Entity Type

Personal Trainer

Requirements
Must have
• My name with my info:
Delphine R. Ashcroft (BHK)
NFBP Certified Clinical Exercise Specialist & Personal Trainer
del.ashcroft@talloakfitness.example
Cell: 555-302-6148

Please make it double sided.
Nice to have
• An image that represents cardiac and general fitness training.

```html
<!DOCTYPE html>
<html lang="en">
<head>
<meta charset="utf-8">
<title>Tall Oak Fitness – Business Card</title>
<link rel="stylesheet" href="https://fonts.googleapis.com/css2?family=Questrial&family=Mulish:wght@400;700&display=swap">
<style>
  :root {
    --backdrop: #e9e7e3;
    --card: #f6f6f4;
    --ink: #222222;
    --ink-soft: #333333;
    --accent: #d9232b;
    --accent-dark: #a8171d;
  }
  * { margin: 0; padding: 0; box-sizing: border-box; }
  html, body {
    width: 1200px;
    height: 900px;
    overflow: hidden;
    background: var(--backdrop);
  }
  .canvas {
    position: relative;
    width: 1200px;
    height: 900px;
  }
  .card {
    position: absolute;
    left: 100px;
    top: 164px;
    width: 1000px;
    height: 572px;
    background: var(--card);
    box-shadow: 0 6px 24px rgba(0,0,0,0.12);
    overflow: hidden;
  }
  .card__ribbon {
    position: absolute;
    left: 0;
    top: 0;
    width: 1000px;
    height: 140px;
  }
  .card__ribbon-band { fill: var(--accent); }
  .card__ribbon-fold { fill: var(--accent-dark); }
  .brand-name {
    position: absolute;
    left: 56px;
    top: 108px;
    font-family: "Questrial", sans-serif;
    font-size: 56px;
    letter-spacing: 1px;
    color: var(--ink);
    white-space: nowrap;
  }
  .person {
    position: absolute;
    left: 72px;
    top: 288px;
  }
  .person__name {
    font-family: "Mulish", sans-serif;
    font-weight: 700;
    font-size: 31px;
    color: var(--ink);
    line-height: 1.2;
  }
  .person__title {
    font-family: "Mulish", sans-serif;
    font-weight: 400;
    font-size: 24px;
    color: var(--ink-soft);
    line-height: 1.3;
  }
  .contact {
    position: absolute;
    left: 72px;
    top: 420px;
    list-style: none;
    font-family: "Mulish", sans-serif;
    font-size: 27px;
    color: var(--ink);
  }
  .contact__item {
    display: flex;
    align-items: center;
    gap: 14px;
    line-height: 44px;
  }
  .contact__icon {
    width: 20px;
    height: 20px;
    fill: var(--ink);
    flex: none;
  }
</style>
</head>
<body>
<main class="canvas">
  <section class="card" aria-label="Tall Oak Fitness business card, front">
    <svg class="card__ribbon" viewBox="0 0 1000 140" aria-hidden="true">
      <polygon class="card__ribbon-fold" points="612,66 650,66 650,128 628,128 612,112"/>
      <polygon class="card__ribbon-band" points="632,30 1000,22 1000,112 650,120 650,90 632,86"/>
    </svg>

    <div class="brand-name">Tall Oak Fitness</div>

    <div class="person">
      <p class="person__name">Delphine R. Ashcroft (BHK)</p>
      <p class="person__title">NFBP Certified Clinical Exercise Specialist &amp; Personal Trainer</p>
    </div>

    <ul class="contact">
      <li class="contact__item">
        <svg class="contact__icon" viewBox="0 0 24 24" aria-hidden="true">
          <path d="M6.6 10.8a15.1 15.1 0 0 0 6.6 6.6l2.2-2.2a1 1 0 0 1 1-.25 11.4 11.4 0 0 0 3.6.57 1 1 0 0 1 1 1V20a1 1 0 0 1-1 1A17 17 0 0 1 3 4a1 1 0 0 1 1-1h3.5a1 1 0 0 1 1 1c0 1.25.2 2.45.57 3.57a1 1 0 0 1-.25 1z"/>
        </svg>
        <span>555-302-6148</span>
      </li>
      <li class="contact__item">
        <svg class="contact__icon" viewBox="0 0 24 24" aria-hidden="true">
          <path d="M2 5h20v14H2z M3.5 6.5 12 13l8.5-6.5" fill="none" stroke="#222" stroke-width="2"/>
          <path d="M2 5h20L12 13z"/>
        </svg>
        <span>del.ashcroft@talloakfitness.example</span>
      </li>
    </ul>
  </section>
</main>
</body>
</html>
```